Online interactive tutorial for year 2 to year 12 students in Australia

Website design for a new online tutorial for year 2 to year 12 students in Australia.

- The tutorial will be conducted via live webcam and within a dedicated interactive space
- The tutorial will be provided by high scoring undergraduates studying in top Australian universities.
- The tutors will be going through interviews & assessments & only top students are allowed to apply.
- Parents will do search and select tutor and have short 15 mins video interaction with potential tutors before booking them for their children for tutoring.
- hourly cost of booking (no monthly subscription or no hour limits)
- Tutors will have their own profile

Please see the attached for detailed page functionality.

The look and feel of the design must consider the following:
- must be educational but not dull and should stand out
- must appeal to younger generation - tutees (8-18 years), tutors (19-25), parents (30-50).
- Ideas for Logos (brivora.com.au but not confirmed)

Target Market(s)

tutees (8-18 years), tutors (19-25 years), parents (30-50 years).

Industry/Entity Type

Education

Coding

Coded - Design and coding required

Number of Pages Required

5+ page

Font styles to use
Serif

Requirements
Must have
• The look and feel of the design must consider the following:
• - must be educational but not dull and should stand out
• - must appeal to younger generation - tutees (8-18 years), tutors (19-25), parents (30-50).
Should not have
• Dullness

```html
<!DOCTYPE html>
<html lang="en">
<head>
<meta charset="utf-8">
<title>Brivora – Online Tutoring</title>
<link href="https://fonts.googleapis.com/css2?family=Oswald:wght@400;500;600&family=Open+Sans:wght@400;600;700&display=swap" rel="stylesheet">
<style>
:root{
  --blue:#1e88c9;
  --blue-dark:#15679c;
  --orange:#f5a01a;
  --red:#e5323b;
  --green:#34b44a;
  --purple:#7b3fa0;
  --ink:#2d3338;
  --muted:#7b8288;
  --line:#e4e7ea;
  --dark:#1b1f23;
  --footer:#222a31;
  --footer-deep:#171c21;
  --white:#fff;
  --yellow:#ffd43b;
}
*{box-sizing:border-box;margin:0;padding:0}
html,body{width:1200px;height:2416px;overflow:hidden}
body{font-family:"Open Sans",Arial,sans-serif;color:var(--ink);background:var(--white);position:relative}
.head{font-family:"Oswald",Arial,sans-serif;text-transform:uppercase}

/* header */
.site-header{height:70px;display:flex;align-items:center;padding:0 70px;background:var(--white);position:relative;z-index:2}
.brand{display:flex;align-items:center;gap:10px}
.brand-mark{width:30px;height:30px;background:var(--blue);border-radius:4px}
.brand-name{font-family:"Oswald",sans-serif;font-weight:600;font-size:26px;color:var(--ink);letter-spacing:1px}
.main-nav{margin-left:auto;display:flex;align-items:center;gap:22px;font-size:11px;font-weight:600;text-transform:uppercase}
.main-nav a{color:var(--ink);text-decoration:none}
.main-nav a.active{color:var(--blue);border-bottom:2px solid var(--blue);padding-bottom:4px}
.search-btn{width:30px;height:30px;border:1px solid var(--line);border-radius:50%;display:flex;align-items:center;justify-content:center}
.login-btn{background:var(--red);color:var(--white)!important;padding:10px 18px;border-radius:3px}

/* hero */
.hero{position:absolute;top:70px;left:0;width:1200px;height:530px;overflow:hidden}
.hero-photo{position:absolute;inset:0;background:linear-gradient(100deg,#e9c27d 0%,#d8b07a 22%,#4e86ad 42%,#2f6f9e 70%,#245e8b 100%)}
.hero-text{position:absolute;left:700px;top:190px;color:var(--white)}
.hero-text h1{font-family:"Oswald",sans-serif;font-weight:500;font-size:50px;letter-spacing:2px;line-height:1}
.hero-text p{font-family:"Oswald",sans-serif;font-size:32px;color:var(--yellow);margin-top:8px}
.hero-actions{display:flex;gap:12px;margin-top:26px}
.btn{display:inline-block;font-family:"Oswald",sans-serif;font-size:13px;text-transform:uppercase;color:var(--white);padding:11px 20px;border-radius:3px;letter-spacing:.5px}
.btn-orange{background:var(--orange)}
.btn-red{background:var(--red)}
.slider-arrows{position:absolute;right:40px;bottom:22px;display:flex;gap:6px}
.slider-arrows span{width:24px;height:24px;border-radius:50%;background:rgba(255,255,255,.35)}

/* section titles */
.section-title{font-family:"Oswald",sans-serif;font-size:34px;font-weight:500;text-align:center;text-transform:uppercase}
.section-title::after{content:"";display:block;width:60px;height:3px;background:var(--blue);margin:10px auto 0}
.section-sub{font-size:12px;color:var(--muted);text-align:center;margin-top:14px}

/* services */
.services{position:absolute;top:600px;left:0;width:1200px;height:460px;padding-top:58px;background:var(--white)}
.service-grid{display:flex;gap:22px;justify-content:center;margin-top:40px}
.service-card{width:240px;height:240px;color:var(--white);text-align:center;padding:34px 22px 0}
.service-card .icon{width:64px;height:64px;margin:0 auto 18px;display:flex;align-items:center;justify-content:center}
.service-card h3{font-family:"Oswald",sans-serif;font-weight:500;font-size:15px;text-transform:uppercase;margin-bottom:10px}
.service-card p{font-size:11.5px;line-height:1.6;opacity:.95}
.s-orange{background:var(--orange)}.s-blue{background:var(--blue)}.s-green{background:var(--green)}.s-purple{background:var(--purple)}

/* how it works */
.how{position:absolute;top:1060px;left:0;width:1200px;height:520px;background:linear-gradient(180deg,#191c20,#23282e);color:var(--white)}
.how-title{position:absolute;left:90px;top:50px;font-family:"Oswald",sans-serif;font-size:34px;font-weight:500}
.how-sub{position:absolute;left:90px;top:104px;font-size:11.5px;color:#c8cdd2;width:700px}
.video{position:absolute;left:90px;top:150px;width:380px;height:220px;background:linear-gradient(135deg,#c9a988,#e7d3b6 55%,#b48c6a)}
.play{position:absolute;left:160px;top:80px;width:60px;height:60px;border-radius:50%;background:rgba(20,20,20,.75);display:flex;align-items:center;justify-content:center}
.how-copy{position:absolute;left:500px;top:150px;width:300px;font-size:11.5px;line-height:1.65;color:#d4d8dc}
.how-copy p{margin-bottom:14px}
.how-copy .btn{margin-top:4px}
.register{position:absolute;left:840px;top:60px;width:270px;height:400px;background:var(--white);color:var(--ink);padding:24px 26px}
.register h4{font-family:"Oswald",sans-serif;font-weight:500;font-size:16px;text-align:center;text-transform:uppercase;border-bottom:1px solid var(--line);padding-bottom:14px;margin-bottom:20px}
.field{height:38px;border:1px solid var(--line);border-radius:3px;margin-bottom:14px;font-size:11.5px;color:var(--muted);display:flex;align-items:center;justify-content:center}
.register .submit{height:40px;background:var(--blue);color:var(--white);display:flex;align-items:center;justify-content:center;font-family:"Oswald",sans-serif;font-size:14px;border-radius:3px;margin-top:8px}

/* tutors */
.tutors{position:absolute;top:1580px;left:0;width:1200px;height:640px;background:#f6f7f8;padding-top:46px}
.tutor-grid{display:flex;gap:30px;justify-content:center;margin-top:42px}
.tutor-card{width:320px;height:440px;background:var(--white);border:1px solid var(--line);position:relative}
.tutor-band{height:70px;color:var(--white);font-family:"Oswald",sans-serif;font-size:14px;text-align:center;padding-top:14px}
.band-orange{background:var(--orange)}.band-blue{background:var(--blue)}
.avatar{width:96px;height:96px;border-radius:50%;background:linear-gradient(160deg,#c9ced3,#8e979f);border:4px solid var(--white);margin:-30px auto 0;position:relative}
.tutor-bio{font-size:11.5px;color:var(--muted);text-align:center;line-height:1.6;padding:16px 26px 14px}
.tutor-rows{padding:0 26px}
.tutor-row{display:flex;justify-content:space-between;font-size:11.5px;border-top:1px solid var(--line);padding:11px 0}
.tutor-row span:first-child{display:flex;align-items:center;gap:8px;font-weight:600}
.tutor-row span:last-child{color:var(--muted)}
.tutor-link{position:absolute;bottom:20px;left:0;right:0;text-align:center;font-size:11.5px;color:var(--blue);font-weight:600}

/* footer */
.site-footer{position:absolute;top:2220px;left:0;width:1200px;height:196px;background:var(--footer);color:#c3c8cd}
.footer-cols{display:flex;padding:20px 90px 0;gap:40px;height:160px}
.footer-col{width:230px;font-size:11px;line-height:1.7}
.footer-col h5{font-family:"Oswald",sans-serif;color:var(--white);font-weight:500;font-size:14px;text-transform:uppercase;margin-bottom:8px}
.footer-col .item{display:flex;gap:8px;align-items:flex-start;margin-bottom:4px}
.dot{width:8px;height:8px;background:var(--blue);border-radius:50%;margin-top:5px;flex:none}
.footer-col .accent{color:var(--blue)}
.footer-col.social{width:160px}
.footer-bottom{height:36px;background:var(--footer-deep);font-size:10.5px;display:flex;align-items:center;justify-content:center;color:#8d949a;letter-spacing:.5px}
</style>
</head>
<body>

<header class="site-header">
  <div class="brand"><span class="brand-mark"></span><span class="brand-name">BRIVORA</span></div>
  <nav class="main-nav">
    <a class="active" href="#">Home</a><a href="#">About Us</a><a href="#">Services</a><a href="#">How It Works</a>
    <a href="#">Courses</a><a href="#">Schedules</a><a href="#">Events</a><a href="#">Contact Us</a>
    <span class="search-btn"><svg width="12" height="12" viewBox="0 0 12 12"><circle cx="5" cy="5" r="3.8" fill="none" stroke="#2d3338" stroke-width="1.5"/><line x1="8" y1="8" x2="11" y2="11" stroke="#2d3338" stroke-width="1.5"/></svg></span>
    <a class="login-btn" href="#">Student Login</a>
  </nav>
</header>

<section class="hero">
  <div class="hero-photo" role="img" aria-label="Smiling boy using a laptop in front of a chalkboard covered with maths"></div>
  <div class="hero-text">
    <h1>ONLINE TRAINING</h1>
    <p>kids from 2 years to 12 years</p>
    <div class="hero-actions"><span class="btn btn-orange">Book Registration</span><span class="btn btn-red">Free Registration</span></div>
  </div>
  <div class="slider-arrows"><span></span><span></span></div>
</section>

<section class="services">
  <h2 class="section-title">Our Services</h2>
  <p class="section-sub">Live tutoring by top undergraduates for students from year 2 to year 12, with flexible hourly booking and no monthly fees.</p>
  <div class="service-grid">
    <div class="service-card s-orange">
      <div class="icon"><svg width="56" height="48" viewBox="0 0 56 48"><rect x="4" y="4" width="48" height="30" rx="3" fill="none" stroke="#fff" stroke-width="3"/><circle cx="28" cy="19" r="6" fill="#fff"/><rect x="18" y="38" width="20" height="4" fill="#fff"/></svg></div>
      <h3>Live Webcam</h3>
      <p>Face to face lessons in a dedicated interactive space, right from home.</p>
    </div>
    <div class="service-card s-blue">
      <div class="icon"><svg width="60" height="44" viewBox="0 0 60 44"><polygon points="30,4 58,16 30,28 2,16" fill="#fff"/><path d="M14 22v10c0 5 32 5 32 0V22l-16 7z" fill="#fff"/></svg></div>
      <h3>High Scoring Undergraduates</h3>
      <p>Tutors study at leading Australian universities and know the course.</p>
    </div>
    <div class="service-card s-green">
      <div class="icon"><svg width="48" height="52" viewBox="0 0 48 52"><rect x="6" y="4" width="36" height="44" rx="3" fill="none" stroke="#fff" stroke-width="3"/><polyline points="14,26 22,34 35,18" fill="none" stroke="#fff" stroke-width="4"/></svg></div>
      <h3>Interviews &amp; Assessments</h3>
      <p>Every tutor is interviewed and assessed; only top students are accepted.</p>
    </div>
    <div class="service-card s-purple">
      <div class="icon"><svg width="58" height="40" viewBox="0 0 58 40"><rect x="2" y="6" width="38" height="28" rx="4" fill="#fff"/><polygon points="42,20 56,8 56,32" fill="#fff"/></svg></div>
      <h3>Video Interaction</h3>
      <p>Parents meet a tutor in a free 15 minute video call before booking.</p>
    </div>
  </div>
</section>

<section class="how">
  <h2 class="how-title head">How It Works</h2>
  <p class="how-sub">Search for a tutor, meet them on video, then book lessons by the hour with no limits.</p>
  <div class="video" role="img" aria-label="Video still of children learning together at a table">
    <span class="play"><svg width="22" height="24" viewBox="0 0 22 24"><polygon points="4,2 20,12 4,22" fill="#fff"/></svg></span>
  </div>
  <div class="how-copy">
    <p>Parents browse tutor profiles by subject, year level and availability, then pick the best match for their child.</p>
    <p>A short video chat lets everyone say hello first. Once happy, book hourly sessions that suit your family's week.</p>
    <p>Lessons run live over webcam with shared whiteboards, notes and practice tasks.</p>
    <span class="btn btn-orange">View More</span>
  </div>
  <form class="register">
    <h4>Register</h4>
    <div class="field">Name</div>
    <div class="field">E-mail</div>
    <div class="field">Password</div>
    <div class="field">Confirm Password</div>
    <div class="submit">REGISTER</div>
  </form>
</section>

<section class="tutors">
  <h2 class="section-title">Tutors Profile</h2>
  <p class="section-sub">Get to know our tutors, their subjects and how to reach them before you book.</p>
  <div class="tutor-grid">
    <article class="tutor-card">
      <div class="tutor-band band-orange">JOHN DOE – Master Of Marketing</div>
      <div class="avatar" role="img" aria-label="Tutor portrait photo"></div>
      <p class="tutor-bio">Friendly tutor covering maths and English for primary and high school students.</p>
      <div class="tutor-rows">
        <div class="tutor-row"><span>Date Position</span><span>Leader / Tutor</span></div>
        <div class="tutor-row"><span>Email</span><span>john@brivora.com.au</span></div>
        <div class="tutor-row"><span>Mobile</span><span>0400 000 000</span></div>
      </div>
      <div class="tutor-link">Click Here More Details</div>
    </article>
    <article class="tutor-card">
      <div class="tutor-band band-blue">JOHN DOE – Master Of Marketing</div>
      <div class="avatar" role="img" aria-label="Tutor portrait photo"></div>
      <p class="tutor-bio">Friendly tutor covering science and business studies for senior students.</p>
      <div class="tutor-rows">
        <div class="tutor-row"><span>Date Position</span><span>Leader / Tutor</span></div>
        <div class="tutor-row"><span>Email</span><span>john@brivora.com.au</span></div>
        <div class="tutor-row"><span>Mobile</span><span>0400 000 000</span></div>
      </div>
      <div class="tutor-link">Click Here More Details</div>
    </article>
    <article class="tutor-card">
      <div class="tutor-band band-orange">JOHN DOE – Master Of Marketing</div>
      <div class="avatar" role="img" aria-label="Tutor portrait photo"></div>
      <p class="tutor-bio">Friendly tutor covering chemistry and physics for year 11 and 12 students.</p>
      <div class="tutor-rows">
        <div class="tutor-row"><span>Date Position</span><span>Leader / Tutor</span></div>
        <div class="tutor-row"><span>Email</span><span>john@brivora.com.au</span></div>
        <div class="tutor-row"><span>Mobile</span><span>0400 000 000</span></div>
      </div>
      <div class="tutor-link">Click Here More Details</div>
    </article>
  </div>
</section>

<footer class="site-footer">
  <div class="footer-cols">
    <div class="footer-col">
      <h5>Contact Us</h5>
      <div class="item"><span class="dot"></span><span>48 Harbour Lane, Sydney NSW</span></div>
      <div class="item"><span class="dot"></span><span>+61 2 5550 1842</span></div>
      <div class="item"><span class="dot"></span><span>info@brivora.com.au</span></div>
    </div>
    <div class="footer-col">
      <h5>Latest Tweet's</h5>
      <div class="item"><span class="dot"></span><span>New tutors joined this week, book a free chat <span class="accent">brivora.com.au</span></span></div>
      <div class="item"><span class="dot"></span><span>Exam prep sessions open for term four <span class="accent">brivora.com.au</span></span></div>
    </div>
    <div class="footer-col">
      <h5>Recent Updates</h5>
      <div class="item"><span class="dot"></span><span>Holiday tutoring timetable now live. <span class="accent">12 Sept, 2016</span></span></div>
      <div class="item"><span class="dot"></span><span>Parent guide to choosing a tutor. <span class="accent">28 Aug, 2016</span></span></div>
    </div>
    <div class="footer-col social">
      <h5>Social Media</h5>
      <div class="item"><span class="dot"></span><span>Community Page</span></div>
      <div class="item"><span class="dot"></span><span>News Feed</span></div>
      <div class="item"><span class="dot"></span><span>Photo Gallery</span></div>
      <div class="item"><span class="dot"></span><span>Video Channel</span></div>
    </div>
  </div>
  <div class="footer-bottom">© 2016 BRIVORA | ALL RIGHTS RESERVED</div>
</footer>

</body>
</html>
```